RTavenor Business Cards & Letterhead

I have a logo but need a design for some new business cards. We are a Design-Build Firm that specializes in the design and construction of commercial projects.
the cards need to be professional. no cartoon stuff.
i would like to have the cards in AI format so I can update the card as needed. Logo is provided.
Our Address is: 4187 Marlowe Ct. Orrin Falls, Westmark 27614

```html
<!DOCTYPE html>
<html lang="en">
<head>
<meta charset="utf-8">
<title>RTavenor Business Card</title>
<link rel="stylesheet" href="https://fonts.googleapis.com/css2?family=Open+Sans:wght@400;600;700;800&display=swap">
<style>
  :root {
    --page: #e9e7e4;
    --card: #1f2024;
    --card-deep: #141518;
    --ink-grey: #7d7f84;
    --ink-light: #d9dadc;
    --ink-white: #ffffff;
    --accent: #1874c4;
    --accent-deep: #0d4f8f;
  }
  * { box-sizing: border-box; margin: 0; padding: 0; }
  html, body { width: 1200px; height: 780px; overflow: hidden; background: var(--page); }
  .canvas {
    position: relative; width: 1200px; height: 780px;
    display: flex; align-items: center; justify-content: center; gap: 40px;
    font-family: "Open Sans", Arial, sans-serif;
  }
  .card {
    position: relative; width: 540px; height: 309px;
    background: var(--card); overflow: hidden;
    box-shadow: 0 10px 28px rgba(0,0,0,.28);
  }
  /* front */
  .brand {
    position: absolute; left: 30px; top: 28px;
    display: flex; align-items: center; gap: 10px;
  }
  .brand-square { width: 22px; height: 22px; background: var(--accent); }
  .brand-name {
    font-weight: 800; font-size: 30px; letter-spacing: 1px;
    color: var(--ink-grey); line-height: 1;
  }
  .address {
    position: absolute; left: 30px; top: 96px;
    font-size: 13px; line-height: 1.35; color: var(--ink-light);
  }
  .contacts {
    position: absolute; left: 30px; top: 146px; list-style: none;
    font-size: 13px; line-height: 1.55; color: var(--ink-light);
  }
  .contacts li { display: flex; align-items: center; gap: 7px; }
  .contacts svg { width: 11px; height: 11px; flex: none; }
  .person {
    position: absolute; right: 34px; top: 82px; text-align: right;
  }
  .person-name {
    font-weight: 700; font-size: 21px; letter-spacing: .5px;
    color: var(--accent); text-transform: uppercase; line-height: 1.1;
  }
  .person-title { font-size: 14px; color: var(--ink-white); margin-top: 4px; }
  .accent-tab {
    position: absolute; right: 0; top: 82px; width: 14px; height: 48px;
    background: linear-gradient(180deg, var(--accent), var(--accent-deep));
  }
  .monogram-area {
    position: absolute; left: 250px; bottom: 0; width: 210px; height: 150px;
    background: linear-gradient(135deg, var(--card-deep) 0%, #2b2c31 60%, #4a4b50 100%);
  }
  /* back */
  .pattern-area {
    position: absolute; inset: 0;
    background: radial-gradient(ellipse at 40% 40%, #2a2b2f 0%, #1b1c1f 70%, #151619 100%);
  }
  .back .brand {
    left: 50%; top: 50%; transform: translate(-50%, -50%); gap: 12px;
  }
  .back .brand-square { width: 26px; height: 26px; }
  .back .brand-name { font-size: 36px; }
</style>
</head>
<body>
<main class="canvas">
  <section class="card front" aria-label="Business card front">
    <div class="brand">
      <span class="brand-square"></span>
      <span class="brand-name">RTAVENOR</span>
    </div>
    <p class="address">4187 Marlowe Ct. Orrin Falls,<br>Westmark 27614</p>
    <ul class="contacts">
      <li>
        <svg viewBox="0 0 12 12"><path fill="var(--accent)" d="M2.5 1l2 2.3-1 1.3a7 7 0 0 0 3.9 3.9l1.3-1L11 9.5 9.6 11C5 10.6 1.4 7 1 2.4z"/></svg>
        (555) 304-0148
      </li>
      <li>
        <svg viewBox="0 0 12 12"><circle cx="6" cy="6" r="5" fill="none" stroke="var(--accent)" stroke-width="1.4"/><path d="M1 6h10M6 1c2.5 2.8 2.5 7.2 0 10M6 1c-2.5 2.8-2.5 7.2 0 10" fill="none" stroke="var(--accent)" stroke-width="1"/></svg>
        www.rtavenor.com
      </li>
      <li>
        <svg viewBox="0 0 12 12"><rect x="1" y="2.5" width="10" height="7" fill="none" stroke="var(--accent)" stroke-width="1.4"/><path d="M1 2.5l5 4 5-4" fill="none" stroke="var(--accent)" stroke-width="1.2"/></svg>
        DRT@RTavenor.com
      </li>
    </ul>
    <div class="person">
      <p class="person-name">Darren Tavenor</p>
      <p class="person-title">Founder/President</p>
    </div>
    <span class="accent-tab"></span>
    <div class="monogram-area" role="img" aria-label="Large glossy monogram decoration"></div>
  </section>

  <section class="card back" aria-label="Business card back">
    <div class="pattern-area" role="img" aria-label="Embossed repeating pattern of the firm's mark"></div>
    <div class="brand">
      <span class="brand-square"></span>
      <span class="brand-name">RTAVENOR</span>
    </div>
  </section>
</main>
</body>
</html>
```